Business card for a Exhibition booth fabrication company

Hi. My company would like to change our corporate name card. We are an events and Exhibition stand builder company. We would like our corporate name card to resonate what we do. I need someone to create something unique that relates to the industry that I am in. The graphic designer should be creative to incorporate the elements of my industry and try to blend in well in the design of the card. Our aim is to ensure that we are unique and our card can look different from our competitors.
Updates

Target Market(s)

Marketing and events manager from all companies

Contact Information for Business Card

The business card should have the following details:
Name
Job Title
Email
Website

Colors

Designer to choose colors to be used in the design.

Requirements
Must have
• The card must be look something that is relevant to the service that I am providing. My website is: www.velmora-buildworks.com
• You can see my website to get more information on what service that I am doing
Nice to have
• On the back of my card, I would like to have a globe image with the incorporation of my company logo. This is to indicate that my services can be done in any part of the world.

```html
<!DOCTYPE html>
<html lang="en">
<head>
<meta charset="utf-8">
<title>Velmora Buildworks – Business Card</title>
<link rel="stylesheet" href="https://fonts.googleapis.com/css2?family=Open+Sans:wght@400;600;700&display=swap">
<style>
  :root {
    --backdrop: #1c1c1e;
    --card-white: #ffffff;
    --brand-red: #ec1c24;
    --band-grey: #5f5f61;
    --wordmark-grey: #555558;
    --map-grey: #c9c9cb;
    --map-grey-soft: #ececed;
    --text-on-red: #ffffff;
  }
  * { box-sizing: border-box; margin: 0; padding: 0; }
  html, body {
    width: 1200px; height: 960px; overflow: hidden;
    background: var(--backdrop);
    font-family: "Open Sans", Arial, sans-serif;
  }
  .canvas {
    position: relative; width: 1200px; height: 960px;
    display: flex; flex-direction: column; align-items: center; justify-content: center; gap: 60px;
  }
  .card {
    position: relative; width: 700px; height: 400px;
    background: var(--card-white);
    border-radius: 6px; overflow: hidden;
    box-shadow: 0 10px 30px rgba(0,0,0,.45);
  }

  /* Back side */
  .world-area {
    position: absolute; left: 120px; top: 22px; width: 500px; height: 250px;
    border-radius: 50% / 60%;
    background: radial-gradient(ellipse at 55% 45%, var(--map-grey) 0%, var(--map-grey-soft) 60%, rgba(255,255,255,0) 72%);
  }
  .back-wordmark {
    position: absolute; left: 0; right: 0; top: 270px;
    display: flex; align-items: center; justify-content: center; gap: 16px;
  }
  .back-wordmark .mark-dot { width: 30px; height: 30px; border-radius: 50%; background: var(--brand-red); }
  .back-wordmark .name {
    font-weight: 600; font-size: 34px; letter-spacing: 4px;
    color: var(--wordmark-grey); text-transform: uppercase;
  }

  /* Front side */
  .front-shape { position: absolute; inset: 0; }
  .front-wordmark {
    position: absolute; left: 40px; top: 112px;
    display: flex; align-items: center; gap: 10px;
  }
  .front-wordmark .mark-dot { width: 20px; height: 20px; border-radius: 50%; background: var(--brand-red); flex: none; }
  .front-wordmark .name {
    font-weight: 600; font-size: 18px; letter-spacing: 2px;
    color: var(--wordmark-grey); text-transform: uppercase; white-space: nowrap;
  }
  .holder {
    position: absolute; right: 34px; top: 42px; text-align: right; color: var(--text-on-red);
  }
  .holder .person { font-weight: 700; font-size: 22px; letter-spacing: 1px; text-transform: uppercase; }
  .holder .role { font-size: 16px; letter-spacing: 2px; text-transform: uppercase; margin-top: 2px; }
  .contact {
    position: absolute; right: 34px; top: 200px; list-style: none;
    text-align: right; color: var(--text-on-red); font-size: 17px; line-height: 29px;
  }
  .contact li { display: flex; justify-content: flex-end; align-items: center; gap: 12px; white-space: nowrap; }
  .contact .icon { width: 18px; height: 18px; flex: none; }
  .contact .plain { padding-right: 30px; }
</style>
</head>
<body>
<main class="canvas">

  <section class="card card-back" aria-label="Card back">
    <div class="world-area" role="img" aria-label="World map in soft grey shading"></div>
    <div class="back-wordmark">
      <span class="mark-dot"></span>
      <span class="name">Velmora Buildworks</span>
    </div>
  </section>

  <section class="card card-front" aria-label="Card front">
    <svg class="front-shape" width="700" height="400" viewBox="0 0 700 400" aria-hidden="true">
      <path d="M380 0 C415 90 395 190 290 255 C210 300 140 340 110 400 L700 400 L700 0 Z" fill="var(--band-grey)"/>
      <path d="M420 0 C455 90 440 200 340 270 C265 318 190 350 160 400 L700 400 L700 0 Z" fill="var(--brand-red)"/>
    </svg>

    <div class="front-wordmark">
      <span class="mark-dot"></span>
      <span class="name">Velmora Buildworks</span>
    </div>

    <div class="holder">
      <p class="person">Dana Whitcombe</p>
      <p class="role">President</p>
    </div>

    <ul class="contact">
      <li class="plain">Street Name, City Name</li>
      <li class="plain">Zipcode - 01234</li>
      <li>012-345-6789
        <svg class="icon" viewBox="0 0 24 24" aria-hidden="true"><path fill="#fff" d="M6.6 10.8a15.1 15.1 0 0 0 6.6 6.6l2.2-2.2c.3-.3.7-.4 1-.2 1.1.4 2.3.6 3.6.6.6 0 1 .4 1 1V20c0 .6-.4 1-1 1A17 17 0 0 1 3 4c0-.6.4-1 1-1h3.5c.6 0 1 .4 1 1 0 1.3.2 2.5.6 3.6.1.3 0 .7-.2 1z"/></svg>
      </li>
      <li>info@velmora-buildworks.com
        <svg class="icon" viewBox="0 0 24 24" aria-hidden="true"><rect x="2" y="5" width="20" height="14" rx="1" fill="#fff"/><path d="M2.5 5.5 12 13l9.5-7.5" fill="none" stroke="var(--brand-red)" stroke-width="1.6"/></svg>
      </li>
      <li>www.velmora-buildworks.com
        <svg class="icon" viewBox="0 0 24 24" aria-hidden="true"><g fill="none" stroke="#fff" stroke-width="1.6"><circle cx="12" cy="12" r="9.5"/><ellipse cx="12" cy="12" rx="4" ry="9.5"/><path d="M2.5 12h19M4 7h16M4 17h16"/></g></svg>
      </li>
    </ul>
  </section>

</main>
</body>
</html>
```